Blue Harbor Inc - Cutting-Edge Biotech Laboratory - Sleek & Sophisticated

Please design a website that has more of a high-tech and high-end feel, with contents outlined in the uploaded file.

Please have main tabs of the following categories: Home, About, FDA & LAWS, Science, Products, Media, Contact.

Media can include all the videos and photos.

Current website: www.blueharborlabs.com - it needs to be much more high-end, sleek and more organized. Please do NOT follow the outlines in the old website, but follow the uploaded CONTENT file.

Target Market(s)

doctors

Industry/Entity Type

Biotechnology

Coding

Coded - Design and coding required

Number of Pages Required

5+ page

Requirements
Must have
• Logo
Nice to have
• Some lotion on the website

```html
<!DOCTYPE html>
<html lang="en">
<head>
<meta charset="utf-8">
<title>Blue Harbor Inc – Regenerative Medicine</title>
<link href="https://fonts.googleapis.com/css2?family=Poppins:wght@400;500;600;700&family=Open+Sans:wght@400;600&display=swap" rel="stylesheet">
<style>
:root{
  --gold:#c29a1e;
  --gold-dark:#a9830f;
  --ink:#2b2b2b;
  --muted:#6f6f6f;
  --line:#e3e3e3;
  --grey-bg:#f1f1f1;
  --footer-bg:#f6f6f6;
  --white:#ffffff;
}
*{box-sizing:border-box;margin:0;padding:0}
html,body{width:1200px;height:3240px;overflow:hidden}
body{font-family:"Open Sans",Arial,sans-serif;color:var(--ink);background:var(--white);position:relative}
h1,h2,h3,h4,.nav,.btn{font-family:"Poppins",Arial,sans-serif}
.photo{display:block}

/* header */
.site-header{position:absolute;top:0;left:0;width:1200px;height:64px;background:var(--white);display:flex;align-items:center;justify-content:space-between;padding:0 40px 0 46px;z-index:3}
.brand{font-family:"Poppins",Arial,sans-serif;font-size:24px;font-weight:600;color:var(--gold);letter-spacing:1px}
.nav{display:flex;gap:34px;font-size:15px;color:#444}
.nav a{color:inherit;text-decoration:none;padding:6px 0}
.nav a.active{color:var(--gold);border-bottom:2px solid var(--gold)}

/* hero */
.hero{position:absolute;top:64px;left:0;width:1200px;height:500px;background:linear-gradient(110deg,#b9c7d3 0%,#e9eef2 35%,#d6dee4 60%,#aebcc7 100%)}
.hero-arrow{position:absolute;top:300px;width:34px;height:64px;background:rgba(0,0,0,.25);display:flex;align-items:center;justify-content:center}
.hero-arrow.left{left:0}.hero-arrow.right{right:0}
.hero-card{position:absolute;top:512px;left:272px;width:656px;height:250px;background:var(--white);border:2px solid var(--gold);display:flex;flex-direction:column;justify-content:center;align-items:center;gap:14px;z-index:2}
.hero-card p{font-family:"Poppins",Arial,sans-serif;font-size:30px;color:#3a3a3a;line-height:1.15}

/* section titles */
.section-title{font-size:30px;font-weight:600;text-align:center;letter-spacing:1px;color:#333}
.section-title::after{content:"";display:block;width:44px;height:3px;background:var(--gold);margin:10px auto 0}

.btn{display:inline-block;background:var(--gold);color:var(--white);font-size:12px;font-weight:500;padding:9px 18px;text-transform:uppercase;letter-spacing:.5px}

/* video */
.video{position:absolute;top:860px;left:160px;width:880px;height:300px}
.video-copy{position:absolute;left:0;top:20px;width:400px}
.video-copy h2{font-size:28px;font-weight:600;margin-bottom:12px}
.video-copy h3{font-size:17px;font-weight:600;line-height:1.35;margin-bottom:14px}
.video-copy p{font-size:12.5px;line-height:1.7;color:var(--muted);margin-bottom:18px}
.video-frame{position:absolute;left:470px;top:20px;width:410px;height:230px;background:linear-gradient(135deg,#6a5145,#a98c74 50%,#5b4436)}
.play{position:absolute;left:175px;top:85px}

/* clinical */
.clinical{position:absolute;top:1200px;left:0;width:1200px;height:480px;background:var(--grey-bg)}
.clinical .section-title{margin-top:40px}
.cards{position:absolute;top:130px;left:160px;display:flex;gap:16px}
.app-card{width:208px;height:270px;background:var(--white)}
.app-card .photo{height:130px}
.app-card h4{font-size:15px;font-weight:500;color:var(--gold);text-align:center;margin:14px 0 10px}
.app-card p{font-size:11px;line-height:1.6;color:var(--muted);text-align:center;padding:0 14px}
.side-arrow{position:absolute;width:30px;height:30px;display:flex;align-items:center;justify-content:center}

/* about */
.about{position:absolute;top:1700px;left:0;width:1200px;height:500px;background:linear-gradient(90deg,#eef1f3,#dfe5e9)}
.about-photo{position:absolute;left:520px;top:0;width:680px;height:500px;background:linear-gradient(120deg,#c8d3dc,#eef2f5 45%,#9eb0be)}
.about h2{position:absolute;left:160px;top:70px;font-size:30px;font-weight:600;color:var(--gold)}
.about h2::after{content:"";display:block;width:44px;height:3px;background:var(--gold);margin-top:8px}
.about-box{position:absolute;left:160px;top:145px;width:370px;padding:26px 28px;background:#ffffff;border-left:3px solid var(--gold)}
.about-box p{font-size:12.5px;line-height:1.75;color:#555;margin-bottom:18px}

/* team */
.team{position:absolute;top:2240px;left:0;width:1200px;height:520px}
.team .section-title{margin-top:26px}
.members{position:absolute;top:100px;left:160px;display:flex;gap:24px}
.member{width:202px;text-align:center}
.member .photo{height:180px;background:linear-gradient(160deg,#dfe4e8,#b6c1ca)}
.member h4{font-size:13px;font-weight:500;letter-spacing:.5px;margin-top:12px;padding:6px 0}
.member.featured h4{background:var(--gold);color:#fff}
.member span{display:block;font-size:11px;color:var(--muted);margin-top:4px}

/* research */
.research{position:absolute;top:2760px;left:0;width:1200px;height:220px;background:radial-gradient(circle at 30% 40%,#cfa526,var(--gold-dark) 70%);text-align:center;color:#fff}
.research h2{font-size:30px;font-weight:600;margin-top:30px}
.research h2::after{content:"";display:block;width:44px;height:3px;background:#fff;margin:8px auto 0}
.research p{width:760px;margin:18px auto 22px;font-size:12.5px;line-height:1.7}
.research .btn{background:transparent;border:1px solid #fff}

/* footer */
.site-footer{position:absolute;top:2980px;left:0;width:1200px;height:200px;background:var(--footer-bg)}
.footer-cols{position:absolute;top:26px;left:160px;display:flex;gap:0}
.footer-col{width:226px;font-size:11.5px;line-height:1.75;color:var(--muted)}
.footer-col:nth-child(2),.footer-col:nth-child(3){width:130px}
.footer-col h4{font-size:14px;font-weight:600;color:#333;margin-bottom:6px}
.socials{display:flex;gap:10px;margin:4px 0 10px}
.socials span{width:22px;height:22px;border-radius:50%;background:#555;display:block}
.copyright{position:absolute;top:3180px;left:0;width:1200px;height:60px;background:#ececec;border-top:1px solid var(--line);text-align:center;font-size:12px;line-height:60px;color:#666}
</style>
</head>
<body>

<header class="site-header">
  <div class="brand">BLUE HARBOR</div>
  <nav class="nav">
    <a class="active">Home</a><a>About</a><a>FDA &amp; Laws</a><a>Science</a><a>Products</a><a>Contact</a>
  </nav>
</header>

<section class="hero photo" role="img" aria-label="Scientists in white coats working with test tubes in a bright laboratory">
  <div class="hero-arrow left"><svg width="14" height="24" viewBox="0 0 14 24"><path d="M12 2 2 12l10 10" fill="none" stroke="#fff" stroke-width="3"/></svg></div>
  <div class="hero-arrow right"><svg width="14" height="24" viewBox="0 0 14 24"><path d="M2 2l10 10L2 22" fill="none" stroke="#fff" stroke-width="3"/></svg></div>
</section>

<div class="hero-card">
  <p>Leader in Regenerative Medicine</p>
  <p>Innovator of the Industry</p>
  <p>Never Compromises on Quality</p>
</div>

<section class="video">
  <div class="video-copy">
    <h2>OUR VIDEO</h2>
    <h3>Interview with Blue Harbor chief<br>scientist Marco Delgado on stem cells</h3>
    <p>Our chief scientist explains how our lab studies cell therapy, why quality control guides every batch, and what doctors should know about safe care. Watch the full interview to learn about our research methods and patient results.</p>
    <span class="btn">Read More</span>
  </div>
  <div class="video-frame photo" role="img" aria-label="Video still of two people seated in an interview set">
    <svg class="play" width="60" height="60" viewBox="0 0 60 60"><circle cx="30" cy="30" r="30" fill="rgba(255,255,255,.9)"/><path d="M24 18l18 12-18 12z" fill="#333"/></svg>
  </div>
</section>

<section class="clinical">
  <h2 class="section-title">CLINICAL APPLICATIONS</h2>
  <div class="side-arrow" style="left:118px;top:255px"><svg width="14" height="24" viewBox="0 0 14 24"><path d="M12 2 2 12l10 10" fill="none" stroke="#999" stroke-width="3"/></svg></div>
  <div class="side-arrow" style="right:118px;top:255px"><svg width="14" height="24" viewBox="0 0 14 24"><path d="M2 2l10 10L2 22" fill="none" stroke="#999" stroke-width="3"/></svg></div>
  <div class="cards">
    <article class="app-card"><div class="photo" role="img" aria-label="Person holding a sore knee" style="background:linear-gradient(135deg,#e9c3a8,#c98a63)"></div><h4>Orthopedics</h4><p>Cell care to help joints, bones and soft tissue heal with less pain.</p></article>
    <article class="app-card"><div class="photo" role="img" aria-label="Runner resting on a park path" style="background:linear-gradient(135deg,#a6c07e,#6d8a4c)"></div><h4>Sports Medicine</h4><p>Support for athletes who want a faster, safer return to their sport.</p></article>
    <article class="app-card"><div class="photo" role="img" aria-label="Nurse dressing a patient wound" style="background:linear-gradient(135deg,#d7b9b0,#9f7b79)"></div><h4>Wound Care</h4><p>Advanced care that helps slow wounds close and skin repair itself.</p></article>
    <article class="app-card"><div class="photo" role="img" aria-label="Doctor examining a patient foot" style="background:linear-gradient(135deg,#cfe0e8,#86a7b6)"></div><h4>Podiatry</h4><p>Treatment options for foot and ankle injuries and daily foot pain.</p></article>
  </div>
</section>

<section class="about">
  <div class="about-photo photo" role="img" aria-label="Scientist in a white coat looking through lab equipment"></div>
  <h2>ABOUT</h2>
  <div class="about-box">
    <p>Blue Harbor Inc provides cell therapy products to doctors who want safe, proven options for their patients. Our team of scientists follows strict lab standards, and every product is tested for purity and quality before it leaves our facility. We work with clinics across the country to share research, train staff and improve patient care.</p>
    <span class="btn">Read More</span>
  </div>
</section>

<section class="team">
  <h2 class="section-title">TEAM</h2>
  <div class="side-arrow" style="left:88px;top:180px"><svg width="14" height="24" viewBox="0 0 14 24"><path d="M12 2 2 12l10 10" fill="none" stroke="#999" stroke-width="3"/></svg></div>
  <div class="side-arrow" style="right:88px;top:180px"><svg width="14" height="24" viewBox="0 0 14 24"><path d="M2 2l10 10L2 22" fill="none" stroke="#999" stroke-width="3"/></svg></div>
  <div class="members">
    <div class="member featured"><div class="photo" role="img" aria-label="Portrait of the chief scientist"></div><h4>MARCO DELGADO</h4><span>Chief Scientist</span></div>
    <div class="member"><div class="photo" role="img" aria-label="Portrait of the project manager"></div><h4>NINA CARVER</h4><span>Stem Cell Project Manager</span></div>
    <div class="member"><div class="photo" role="img" aria-label="Portrait of a physician advisor"></div><h4>DR. OWEN L. PRICE</h4><span>Advisor, Cardiac Longevity</span></div>
    <div class="member"><div class="photo" role="img" aria-label="Portrait of a medical director"></div><h4>DR. PAUL HARTWELL</h4><span>Medical Director</span></div>
  </div>
</section>

<section class="research">
  <h2>RESEARCH</h2>
  <p>Blue Harbor Inc runs clinical studies with partner clinics to measure how cell therapy supports healing. Our findings are shared with doctors so they can make informed choices and give their patients the best possible care and results.</p>
  <span class="btn">Read More</span>
</section>

<footer class="site-footer">
  <div class="footer-cols">
    <div class="footer-col"><h4>Contact</h4>4820 Harbor Point Drive<br>Bayview, CA 90210<br>info@blueharborlabs.com<br>Main line: (555) 014-2290<br>Fax line: (555) 014-2291</div>
    <div class="footer-col"><h4>Links</h4>Home<br>About<br>FDA &amp; Laws<br>Science<br>Products</div>
    <div class="footer-col"><h4>What We Do</h4>Orthopedics<br>Sports Medicine<br>Wound Care<br>Podiatry<br>Research</div>
    <div class="footer-col"><h4>Connect</h4><div class="socials"><span></span><span></span><span></span><span></span></div><h4>Policies</h4>Privacy<br>Complaints and Feedback</div>
    <div class="footer-col"><h4>Other Links</h4>Media<br>Videos<br>Photos<br>Careers<br>Contact</div>
  </div>
</footer>
<div class="copyright">© 2016 Blue Harbor Inc. All Rights Reserved. Privacy Policy | Terms of Use</div>

</body>
</html>
```